Catalogue Design Project

We need a catalog design for a new private university called Redwell Institute Bayshore (see website www.rwi-bs.org). The catalog should be about 30 pages maximum and will include items such as General Information, Academic schedule, department descriptions, program descriptions, course descriptions, school policies, student services, admissions, San diego Lifestyle, etc.
I will provide the text but I need a professional design with regard to page layouts. I have provided some examples.
Ok, i posted the catalog content, just missing course descriptions.
Target Market(s)
Young Professionals, Foreign Students
Industry/Entity Type
University
Look and feel
Each slider illustrates characteristics of the customer's brand and the style your logo design should communicate.

```html
<!DOCTYPE html>
<html lang="en">
<head>
<meta charset="utf-8">
<title>Redwell Institute Programs</title>
<link rel="stylesheet" href="https://fonts.googleapis.com/css2?family=Arvo:wght@700&family=Open+Sans:wght@400&family=Electrolize&family=Michroma&display=swap">
<style>
  :root {
    --ink: #111111;
    --muted: #8a8a8a;
    --brand-blue: #2e6197;
    --rule-blue: #7d9cc0;
    --dot-grey: #a5a5a5;
    --alert-red: #d0262f;
    --paper: #ffffff;
  }
  html, body { margin: 0; padding: 0; overflow: hidden; background: var(--paper); }
  .page {
    position: relative; width: 927px; height: 1200px; overflow: hidden;
    background: var(--paper); color: var(--ink);
    font-family: "Open Sans", "Segoe UI", sans-serif;
  }
  .brand-mark {
    position: absolute; left: 33px; top: 40px; width: 156px; height: 33px;
    border-radius: 10px;
    background: linear-gradient(90deg, #9fb1c6 0%, #b4b4b4 45%, #a9b3c0 70%, #c2c2c2 100%);
  }
  .header-photo {
    position: absolute; left: 636px; top: 33px; width: 291px; height: 112px;
    background: linear-gradient(90deg, rgba(255,255,255,1) 0%, rgba(210,214,222,0.6) 35%, #c9b59a 70%, #a58a6c 100%);
  }
  .header-title {
    position: absolute; left: 350px; top: 94px; margin: 0;
    font-family: "Electrolize", sans-serif; font-weight: 400; font-size: 22px;
    letter-spacing: 3.3px; color: #5a5a5a; white-space: nowrap;
  }
  .header-bar { position: absolute; left: 348px; top: 126px; width: 579px; height: 18px; background: var(--brand-blue); }
  .header-rule { position: absolute; left: 0; top: 144px; width: 927px; height: 2px; background: var(--rule-blue); }
  .column { position: absolute; top: 184px; width: 404px; }
  .column--left { left: 28px; }
  .column--right { left: 479px; }
  .section-heading {
    margin: 0 0 14px; text-align: center;
    font-family: "Arvo", serif; font-weight: 700; font-size: 29px; line-height: 44px;
    text-transform: uppercase; color: var(--ink);
  }
  .body-copy {
    margin: 0 0 22px; font-size: 13px; line-height: 20px; text-align: justify;
  }
  .subheading {
    margin: 28px 0 2px; font-family: "Arvo", serif; font-weight: 700;
    font-size: 26px; line-height: 34px; color: var(--ink);
  }
  .degree-line { margin: 0 0 4px; font-size: 22.5px; line-height: 30px; color: var(--muted); }
  .course-list { margin: 0; padding-left: 55px; color: var(--muted); font-size: 16px; line-height: 32px; }
  .column--right .spacer { height: 44px; }
  .notice {
    position: absolute; left: 0; top: 1060px; width: 927px; margin: 0; text-align: center;
    font-family: "Michroma", sans-serif; font-size: 28px; line-height: 36px;
    letter-spacing: 7px; color: var(--alert-red); text-transform: uppercase;
  }
  .footer-rule { position: absolute; left: 0; top: 1147px; width: 927px; height: 2px; background: var(--rule-blue); }
  .corner-ornament {
    position: absolute; left: 842px; top: 1090px; width: 80px; height: 104px;
    border-radius: 50%;
    background: radial-gradient(ellipse at 45% 45%, #4f7fe0 0%, #2a44b0 45%, #1a2f9a 65%, rgba(255,255,255,0) 71%);
  }
  .folio {
    position: absolute; left: 651px; top: 1167px; margin: 0;
    font-size: 12px; letter-spacing: 0.5px; color: #7a7a7a;
  }
</style>
</head>
<body>
<div class="page">
  <div class="brand-mark" role="img" aria-label="Decorative pattern of blue and grey dots"></div>

  <div class="header-photo" role="img" aria-label="Photo of smiling graduates in caps and gowns"></div>
  <p class="header-title">REDWELL INSTITUTE PROGRAMS</p>
  <div class="header-bar"></div>
  <div class="header-rule"></div>

  <section class="column column--left">
    <h2 class="section-heading">School of Media and Communication</h2>
    <p class="body-copy">Text text text text text text text, text, sample text, text, sample text, sample text. Sample text, text text text,an Text text text text text text text, text, sample text, text, sample text, sample text. Sample text, text text text,an Text text text text text text text, text, sample text, text, sample text, sample text.</p>
    <p class="body-copy">Sample text, text text text,an Text text text text text text text, text, sample text, text, sample text, sample text. Sample text, text text text,an text text text text text text text, text, sample text, text, sample text, sample text. Sample text, text text text,an Text text text text text text text, text, sample text, text, sample text, sample text. Sample text, text text text,an Text text text text text text text, text, sample text, text, sample text, sample text. Sample text, text text text,an Text text text text text text text, text.</p>
    <h3 class="subheading">UNDERGRADUATE COURSES</h3>
    <p class="degree-line">Bachelor of Arts with Majors in</p>
    <ul class="course-list">
      <li>Text</li>
      <li>Text</li>
      <li>Text</li>
    </ul>
  </section>

  <section class="column column--right">
    <h2 class="section-heading">College of Letters and Sciences</h2>
    <p class="body-copy">Text text text text text text text, text, sample text, text, sample text, sample text. Sample text, text text text,an Text text text text text text text, text, sample text, text, sample text, sample text. Sample text, text text text,an Text text text text text text text, text, sample text, text, sample text, sample text.</p>
    <p class="body-copy">Sample text, text text text,an Text text text text text text text, text, sample text, text, sample text, sample text. Sample text, text text text,an text text text text text text text, text, sample text, text, sample text, sample text. Sample text, text text text,an Text text text text text text text, text, sample text, text, sample text, sample text. Sample text, text text text,an Text text text text text text text, text, sample text, text, sample text, sample text. Sample text, text text text,an Text text text text text text text, text.</p>
    <div class="spacer"></div>
    <p class="body-copy">Sample text, text text text,an Text text text text text text text, text, sample text, text, sample text, sample text. Sample text, text text text,an text text text text text text text, text, sample text, text, sample text, sample text. Sample text, text text text,an Text text text text text text text, text, sample text, text, sample text, sample text. Sample text, text text text,an Text text text text text text text, text, sample text, text, sample text, sample text. Sample text, text text text,an Text text text text text text text, text.</p>
  </section>

  <p class="notice">Important info important<br>info important info</p>

  <div class="footer-rule"></div>
  <div class="corner-ornament" role="img" aria-label="Decorative blue bird illustration"></div>
  <p class="folio">2:: REDWELL INSTITUTE</p>
</div>
</body>
</html>
```